Musical download and streaming website

hello designers, I want to start up a musical website where users can download and rate music of different genres such as RnB, Hip hop, rock, afro-pop. This website should be attractive and contemporary. There will be a search column for different songs. Music files will be mp3, mwa, and others. I like blue, gold, pink and indigo colors. My website should resemble http://tunovalt.com. There should be good imaginary of music stars on my website.

```html
<!DOCTYPE html>
<html lang="en">
<head>
<meta charset="utf-8">
<title>Velora Tunes</title>
<link rel="stylesheet" href="https://fonts.googleapis.com/css2?family=Open+Sans:wght@400;600;700;800&family=Cabin:wght@400;500;600&display=swap">
<style>
  :root {
    --topline: #f7d94c;
    --ink: #222;
    --text: #444;
    --muted: #888;
    --sky: #34acd6;
    --sky-dark: #2a86a5;
    --button: #2ea3cc;
    --button-dark: #2488ad;
    --gold: #fedb59;
    --gold-light: #fdeb9a;
    --star: #e0c021;
    --coin: #e8c23a;
    --white: #fff;
  }
  * { box-sizing: border-box; margin: 0; padding: 0; }
  html, body { width: 892px; height: 1200px; overflow: hidden; }
  body { position: relative; font-family: "Cabin", sans-serif; color: var(--text); background: var(--sky); }
  .abs { position: absolute; }

  .site-header { left: 0; top: 0; width: 892px; height: 82px; background: var(--white); border-top: 2px solid var(--topline); }
  .brand { left: 82px; top: 34px; display: flex; align-items: center; gap: 8px; font-family: "Open Sans", sans-serif; font-weight: 800; font-size: 20px; color: var(--ink); letter-spacing: 1px; }
  .brand-dot { width: 14px; height: 14px; border-radius: 50%; background: var(--ink); }
  .nav a { position: absolute; top: 37px; font-size: 9.5px; color: var(--ink); text-decoration: none; text-transform: uppercase; letter-spacing: .2px; }
  .nav a.active { color: var(--sky); }
  .nav-underline { left: 408px; top: 76px; width: 53px; height: 6px; background: var(--sky); }
  .signup { left: 723px; top: 25px; width: 86px; height: 34px; border-radius: 2px; background: linear-gradient(var(--button), var(--button-dark)); color: var(--white); font-size: 9.5px; display: flex; align-items: center; justify-content: center; gap: 4px; text-transform: uppercase; }

  .hero { left: 0; top: 82px; width: 892px; height: 336px; background: radial-gradient(ellipse at 70% 40%, #3d3d3f 0%, #1f1f21 70%); }
  .hero-photo { left: 280px; top: 82px; width: 612px; height: 336px; background: radial-gradient(ellipse 45% 60% at 63% 50%, #d9d8c9 0%, #a7a69c 35%, rgba(120,30,30,.55) 55%, rgba(40,40,42,0) 75%); }
  .hero-title { left: 82px; top: 250px; font-family: "Open Sans", sans-serif; font-weight: 700; font-size: 24px; line-height: 32px; color: var(--white); letter-spacing: .3px; white-space: nowrap; }
  .hero-text { left: 82px; top: 284px; width: 360px; font-size: 10.5px; line-height: 19px; color: var(--white); }
  .hero-arrows { left: 83px; top: 338px; display: flex; gap: 5px; }

  .search-band { left: 0; top: 418px; width: 892px; height: 250px; background: radial-gradient(ellipse at 40% 30%, var(--gold-light) 0%, var(--gold) 60%); }
  .search-input { left: 93px; top: 466px; width: 507px; height: 47px; background: var(--white); border-radius: 3px; box-shadow: 0 1px 2px rgba(0,0,0,.15); padding-left: 18px; display: flex; align-items: center; font-size: 10px; color: var(--muted); }
  .search-btn { left: 614px; top: 466px; width: 185px; height: 47px; border-radius: 3px; background: linear-gradient(var(--button), var(--button-dark)); color: var(--white); font-family: "Open Sans", sans-serif; font-weight: 700; font-size: 15px; display: flex; align-items: center; justify-content: center; gap: 6px; text-transform: uppercase; }
  .filters { left: 95px; top: 531px; display: flex; gap: 14px; font-size: 8.5px; color: var(--text); }
  .filters span { display: flex; align-items: center; gap: 4px; }
  .radio { width: 8px; height: 8px; border-radius: 50%; background: #f4f4f4; border: 1px solid #ddd; }
  .radio.on { background: var(--sky); border: 2px solid #e8f5fb; }
  .genres { right: 94px; top: 531px; display: flex; gap: 16px; font-size: 8.5px; color: var(--text); }
  .genres b { font-weight: 500; color: var(--ink); }
  .divider { left: 98px; top: 562px; width: 702px; height: 1px; background: rgba(0,0,0,.1); }
  .alpha { left: 0; top: 578px; width: 892px; text-align: center; font-size: 8.5px; color: var(--text); word-spacing: 3px; }
  .wave { left: 0; top: 620px; }

  .section-title { left: 82px; font-family: "Open Sans", sans-serif; font-weight: 700; font-size: 19px; color: var(--white); text-transform: uppercase; }
  .card { width: 168px; height: 64px; background: var(--white); border-radius: 2px; box-shadow: 0 1px 2px rgba(0,0,0,.12); }
  .card .thumb { position: absolute; left: 10px; top: 11px; width: 58px; height: 41px; border-radius: 2px; }
  .card .title { position: absolute; left: 78px; top: 19px; font-size: 9px; color: var(--ink); }
  .card .date { position: absolute; left: 78px; top: 35px; font-size: 8.5px; color: var(--muted); display: flex; align-items: center; gap: 3px; }
  .card .stars { position: absolute; left: 78px; top: 34px; }

  .site-footer { left: 0; top: 1070px; width: 892px; height: 130px; background: var(--sky-dark); }
  .footer-links { left: 0; top: 1098px; width: 892px; text-align: center; font-size: 8.5px; color: var(--white); }
  .social { left: 396px; top: 1126px; display: flex; gap: 6px; }
  .social span { width: 21px; height: 21px; border-radius: 50%; background: radial-gradient(circle at 40% 35%, #f5d55a, var(--coin)); }
  .copyright { left: 0; top: 1160px; width: 892px; text-align: center; font-size: 8.5px; color: var(--white); }
</style>
</head>
<body>
  <header class="abs site-header"></header>
  <div class="abs brand"><span class="brand-dot"></span>VELORA TUNES</div>
  <nav class="nav">
    <a class="active" style="left:422px">Home</a>
    <a style="left:488px">Latest</a>
    <a style="left:558px">Top Rated</a>
    <a style="left:646px">Contact Us</a>
  </nav>
  <div class="abs nav-underline"></div>
  <div class="abs signup">
    <svg width="8" height="8" viewBox="0 0 8 8"><circle cx="4" cy="2.2" r="2" fill="#fff"/><path d="M0.5 8 Q4 2.5 7.5 8Z" fill="#fff"/></svg>Signup
  </div>

  <section class="abs hero"></section>
  <div class="abs hero-photo" role="img" aria-label="Red headphones lying beside a smartphone showing a treble clef on a dark leather surface"></div>
  <h1 class="abs hero-title">DOWNLOAD LATEST COLLECTIONS</h1>
  <p class="abs hero-text">Lorem ipsum dolor sit amet, consectetur adipiscing elit. Nulla interdum sceleris que facilisis. Ut quis commodo ligula, eget commodo enim.</p>
  <div class="abs hero-arrows">
    <svg width="17" height="17" viewBox="0 0 17 17"><circle cx="8.5" cy="8.5" r="8.5" fill="#fff"/><path d="M10 4.5 6 8.5 10 12.5" stroke="#222" stroke-width="2.2" fill="none"/></svg>
    <svg width="17" height="17" viewBox="0 0 17 17"><circle cx="8.5" cy="8.5" r="8.5" fill="#fff"/><path d="M7 4.5 11 8.5 7 12.5" stroke="#222" stroke-width="2.2" fill="none"/></svg>
  </div>

  <section class="abs search-band"></section>
  <div class="abs search-input">Search Text Here...</div>
  <div class="abs search-btn">
    <svg width="15" height="15" viewBox="0 0 15 15"><circle cx="6" cy="6" r="4.5" stroke="#fff" stroke-width="2.2" fill="none"/><path d="M9.5 9.5 13.5 13.5" stroke="#fff" stroke-width="2.6"/></svg>Search
  </div>
  <div class="abs filters">
    <span><i class="radio on"></i>All</span>
    <span><i class="radio"></i>Top Rated</span>
    <span><i class="radio"></i>Song</span>
    <span><i class="radio"></i>Artist</span>
  </div>
  <div class="abs genres"><span>Select Genres &nbsp; :</span><b>RnB</b><b>Hip hop</b><b>Rock</b><b>Afro-pop</b></div>
  <div class="abs divider"></div>
  <div class="abs alpha">Song Listing &nbsp;: &nbsp;A B C D E F G H I J K L M N O P Q R S T U V W X Y Z</div>
  <svg class="abs wave" width="892" height="60" viewBox="0 0 892 60">
    <path d="M0 8 C150 8 250 44 384 44 C520 44 600 10 720 10 C800 10 850 18 892 22 V60 H0 Z" fill="#34acd6"/>
  </svg>

  <svg width="0" height="0" style="position:absolute"><defs><path id="star" d="M4.5 0 5.6 3.2 9 3.3 6.3 5.4 7.3 8.7 4.5 6.7 1.7 8.7 2.7 5.4 0 3.3 3.4 3.2Z"/></defs></svg>

  <h2 class="abs section-title" style="top:694px">Last Added</h2>

  <div class="abs card" style="left:82px;top:740px"><div class="thumb" style="background:linear-gradient(135deg,#2a2a2a,#7a6a58)" role="img" aria-label="Hands playing a guitar"></div><div class="title">Lorem ipsum dolor</div><div class="date"><svg width="8" height="8" viewBox="0 0 8 8"><rect x=".5" y="1.5" width="7" height="6" fill="none" stroke="#34acd6"/><rect x=".5" y="1.5" width="7" height="2" fill="#34acd6"/></svg>29 Jun 2016</div></div>
  <div class="abs card" style="left:269px;top:740px"><div class="thumb" style="background:linear-gradient(135deg,#c9934f,#e8c58a)" role="img" aria-label="Sheet music pages"></div><div class="title">Vivamus mollis qu</div><div class="date"><svg width="8" height="8" viewBox="0 0 8 8"><rect x=".5" y="1.5" width="7" height="6" fill="none" stroke="#34acd6"/><rect x=".5" y="1.5" width="7" height="2" fill="#34acd6"/></svg>29 Jun 2016</div></div>
  <div class="abs card" style="left:454px;top:740px"><div class="thumb" style="background:linear-gradient(135deg,#8a9099,#e2e4e8)" role="img" aria-label="Fingertips with drawn music notes"></div><div class="title">Fusce ligula ante</div><div class="date"><svg width="8" height="8" viewBox="0 0 8 8"><rect x=".5" y="1.5" width="7" height="6" fill="none" stroke="#34acd6"/><rect x=".5" y="1.5" width="7" height="2" fill="#34acd6"/></svg>29 Jun 2016</div></div>
  <div class="abs card" style="left:641px;top:740px"><div class="thumb" style="background:linear-gradient(135deg,#6f6a5e,#c9c3b3)" role="img" aria-label="Street musician with guitar"></div><div class="title">Quisque non hend</div><div class="date"><svg width="8" height="8" viewBox="0 0 8 8"><rect x=".5" y="1.5" width="7" height="6" fill="none" stroke="#34acd6"/><rect x=".5" y="1.5" width="7" height="2" fill="#34acd6"/></svg>29 Jun 2016</div></div>

  <div class="abs card" style="left:82px;top:822px"><div class="thumb" style="background:linear-gradient(90deg,#1e1e1e,#7a5a48 60%,#3b4a5a)" role="img" aria-label="Vinyl record and record sleeves"></div><div class="title">Duis mollis ex</div><div class="date"><svg width="8" height="8" viewBox="0 0 8 8"><rect x=".5" y="1.5" width="7" height="6" fill="none" stroke="#34acd6"/><rect x=".5" y="1.5" width="7" height="2" fill="#34acd6"/></svg>29 Jun 2016</div></div>
  <div class="abs card" style="left:269px;top:822px"><div class="thumb" style="background:linear-gradient(135deg,#4d6b2e,#a3a454)" role="img" aria-label="Person lying in grass with headphones"></div><div class="title">Donec purus neque</div><div class="date"><svg width="8" height="8" viewBox="0 0 8 8"><rect x=".5" y="1.5" width="7" height="6" fill="none" stroke="#34acd6"/><rect x=".5" y="1.5" width="7" height="2" fill="#34acd6"/></svg>29 Jun 2016</div></div>
  <div class="abs card" style="left:454px;top:822px"><div class="thumb" style="background:linear-gradient(180deg,#cfe6d8,#2d5a45 45%,#0e1a14)" role="img" aria-label="Concert crowd under stage lights"></div><div class="title">Aliquam id tincidun</div><div class="date"><svg width="8" height="8" viewBox="0 0 8 8"><rect x=".5" y="1.5" width="7" height="6" fill="none" stroke="#34acd6"/><rect x=".5" y="1.5" width="7" height="2" fill="#34acd6"/></svg>29 Jun 2016</div></div>
  <div class="abs card" style="left:641px;top:822px"><div class="thumb" style="background:linear-gradient(135deg,#1f2a33,#6b6f72)" role="img" aria-label="Band playing on stage"></div><div class="title">Lorem ipsum dolor</div><div class="date"><svg width="8" height="8" viewBox="0 0 8 8"><rect x=".5" y="1.5" width="7" height="6" fill="none" stroke="#34acd6"/><rect x=".5" y="1.5" width="7" height="2" fill="#34acd6"/></svg>29 Jun 2016</div></div>

  <h2 class="abs section-title" style="top:918px">Top Rated</h2>

  <div class="abs card" style="left:82px;top:964px"><div class="thumb" style="background:linear-gradient(135deg,#2b2b2b,#5a2222)" role="img" aria-label="Headphones and smartphone"></div><div class="title">Lorem ipsum dolor</div><svg class="stars" width="52" height="9" viewBox="0 0 52 9"><g fill="#e0c021"><use href="#star"/><use href="#star" x="10.5"/><use href="#star" x="21"/><use href="#star" x="31.5"/><path d="M46.5 0 47.6 3.2 51 3.3 48.3 5.4 49.3 8.7 46.5 6.7Z" opacity=".4"/><path d="M46.5 0 45.4 3.2 42 3.3 44.7 5.4 43.7 8.7 46.5 6.7Z"/></g></svg></div>
  <div class="abs card" style="left:269px;top:964px"><div class="thumb" style="background:linear-gradient(135deg,#3a2a1e,#7a5638)" role="img" aria-label="Guitar against wooden boards"></div><div class="title">Lorem ipsum dolor</div><svg class="stars" width="52" height="9" viewBox="0 0 52 9"><g fill="#e0c021"><use href="#star"/><use href="#star" x="10.5"/><use href="#star" x="21"/><use href="#star" x="31.5"/><path d="M46.5 0 47.6 3.2 51 3.3 48.3 5.4 49.3 8.7 46.5 6.7Z" opacity=".4"/><path d="M46.5 0 45.4 3.2 42 3.3 44.7 5.4 43.7 8.7 46.5 6.7Z"/></g></svg></div>
  <div class="abs card" style="left:454px;top:964px"><div class="thumb" style="background:linear-gradient(180deg,#111 50%,#d8d2c4 50%)" role="img" aria-label="Piano keys"></div><div class="title">Lorem ipsum dolor</div><svg class="stars" width="52" height="9" viewBox="0 0 52 9"><g fill="#e0c021"><use href="#star"/><use href="#star" x="10.5"/><use href="#star" x="21"/><use href="#star" x="31.5"/><path d="M46.5 0 47.6 3.2 51 3.3 48.3 5.4 49.3 8.7 46.5 6.7Z" opacity=".4"/><path d="M46.5 0 45.4 3.2 42 3.3 44.7 5.4 43.7 8.7 46.5 6.7Z"/></g></svg></div>
  <div class="abs card" style="left:641px;top:964px"><div class="thumb" style="background:linear-gradient(135deg,#e9c8a8,#9a4a2e)" role="img" aria-label="Child playing a guitar"></div><div class="title">Lorem ipsum dolor</div><svg class="stars" width="52" height="9" viewBox="0 0 52 9"><g fill="#e0c021"><use href="#star"/><use href="#star" x="10.5"/><use href="#star" x="21"/><use href="#star" x="31.5"/><path d="M46.5 0 47.6 3.2 51 3.3 48.3 5.4 49.3 8.7 46.5 6.7Z" opacity=".4"/><path d="M46.5 0 45.4 3.2 42 3.3 44.7 5.4 43.7 8.7 46.5 6.7Z"/></g></svg></div>

  <footer class="abs site-footer"></footer>
  <div class="abs footer-links">Home &nbsp;/&nbsp; About &nbsp;/&nbsp; Privacy Policy &nbsp;/&nbsp; Sitemap &nbsp;/&nbsp; Services</div>
  <div class="abs social">
    <span role="img" aria-label="Social link"></span>
    <span role="img" aria-label="Social link"></span>
    <span role="img" aria-label="Social link"></span>
    <span role="img" aria-label="Feed link"></span>
  </div>
  <div class="abs copyright">@2016 Velora Tunes. All Rights Reserved.</div>
</body>
</html>
```